Unique Private Wine Label for Wine Bottles (UPDATED BRIEF)

Updated Brief Oct 15, 2017. Please see below!

I am looking for a unique wine label designs for my wine bottles. I create wine and would like to have wine labels for my bottles. I am looking for a main label and then several additional labels with the same design just with the type of wine listed on the label (see below for wine types). This is private wine for family and friends to consume not commercially produced wine.

I would like a rustic, classic or vintage design with some color in the label. I do have a specific name for the wine which i like to call "Thornfield" . I would like to see different designs.

We would like vintage or classic labels. Please give me a few multiple designs based on above. I also want to have a main label and then incorporate different types of wine into the labels like "Chardonnay" or "Pinot Noir" or "Sauvignon Blanc" or "Caberent Savignon" or "Merlot" below the name of the wine. As an example, the labels will be the same design but the word Sauvignon Blanc will be incorporated into the design for this type of wine label and so on for the other types of wine.

Please let me know if you have any questions.
Updates

Project Deadline Extended
Reason: I Have changed the vision of the design. I would like a classic, rustic or vintage design NOT a beach theme. The brief has been updated as of Oct 15, 2017. Please see updated brief for instructions on new design

Note: I have changed the vision of the design. I would like a classic, rustic or vintage design NOT a beach theme. The brief has been updated as of Oct 15, 2017. Please see updated brief for instructions on new design. I would like new designers to provide new designs! Payment is Guaranteed! Thanks!

Target Market(s)

This is private wine for family and friends to consume not commercially produced wine.

Font styles to use
Decorative
Script

Colors

Designer to choose colors to be used in the design.

Requirements
Must have
• Updated Brief Oct 15, 2017. Please see below!
• I am looking for a unique wine label designs for my wine bottles. I create wine and would like to have wine labels for my bottles. I am looking for a main label and then several additional labels with the same design just with the type of wine listed on the label (see below for wine types). This is private wine for family and friends to consume not commercially produced wine.
• I would like a rustic, classic or vintage design with some color in the label. I do have a specific name for the wine which i like to call "Thornfield". I would like to see different designs.
• We would like vintage or classic labels. Please give me a few multiple designs based on above. I also want to have a main label and then incorporate different types of wine into the labels like "Chardonnay" or "Pinot Noir" or "Sauvignon Blanc" or "Caberent Savignon" or "Merlot" below the name of the wine. As an example, the labels will be the same design but the word Sauvignon Blanc will be incorporated into the design for this type of wine label and so on for the other types of wine.
• Please let me know if you have any questions.
Nice to have
Should not have
• Please see the updated brief instructions above. I DO NOT WANT A BEACH THEME ANYMORE!

```html
<!DOCTYPE html>
<html lang="en">
<head>
<meta charset="utf-8">
<title>Thornfield Vineyards – Wine Label</title>
<link rel="stylesheet" href="https://fonts.googleapis.com/css2?family=IM+Fell+English&family=IM+Fell+English+SC&family=Great+Vibes&display=swap">
<style>
  :root {
    --backdrop: #4a2800;
    --label-cream: #f3f2ea;
    --label-shade: #e4e3da;
    --ink: #2a2623;
    --ink-soft: #6b6660;
    --accent-red: #8e1b1b;
    --vignette-light: #e9e8e1;
    --vignette-dark: #8d8a84;
  }
  * { box-sizing: border-box; margin: 0; padding: 0; }
  html, body {
    width: 696px;
    height: 1200px;
    overflow: hidden;
    background: var(--backdrop);
  }
  .canvas {
    position: relative;
    width: 696px;
    height: 1200px;
  }
  .wine-label {
    position: absolute;
    left: 128px;
    top: 170px;
    width: 440px;
    height: 860px;
  }
  .label-shape {
    position: absolute;
    inset: 0;
  }
  .estate-name {
    font-family: "IM Fell English SC", "IM Fell English", serif;
    font-size: 50px;
    letter-spacing: 3px;
    fill: var(--ink);
  }
  .estate-dot {
    position: absolute;
    left: 215px;
    top: 214px;
    width: 10px;
    height: 10px;
    border-radius: 50%;
    background: var(--accent-red);
  }
  .vineyard-vignette {
    position: absolute;
    left: 62px;
    top: 250px;
    width: 316px;
    height: 208px;
    border-radius: 50%;
    background: radial-gradient(ellipse at 50% 40%, var(--vignette-light) 0%, #c9c7c0 55%, var(--vignette-dark) 100%);
    border: 2px solid #3a3632;
  }
  .wine-type {
    position: absolute;
    left: 0;
    top: 535px;
    width: 100%;
    text-align: center;
    font-family: "IM Fell English", serif;
    font-size: 58px;
    letter-spacing: 2px;
    color: var(--ink);
    line-height: 1;
  }
  .rule {
    position: absolute;
    height: 1px;
    background: var(--ink-soft);
  }
  .rule-upper { left: 100px; width: 240px; top: 612px; }
  .rule-lower { left: 150px; width: 140px; top: 735px; }
  .tasting-note {
    position: absolute;
    left: 30px;
    top: 636px;
    width: 380px;
    text-align: center;
    font-family: "Great Vibes", cursive;
    font-size: 21px;
    line-height: 1.45;
    color: var(--ink);
  }
  .volume {
    position: absolute;
    left: 0;
    top: 765px;
    width: 100%;
    text-align: center;
    font-family: "IM Fell English", serif;
    font-size: 26px;
    color: var(--ink);
  }
</style>
</head>
<body>
<main class="canvas">
  <section class="wine-label">
    <svg class="label-shape" width="440" height="860" viewBox="0 0 440 860" aria-hidden="true">
      <defs>
        <linearGradient id="labelFill" x1="0" y1="0" x2="0" y2="1">
          <stop offset="0" stop-color="var(--label-shade)"/>
          <stop offset="0.04" stop-color="var(--label-cream)"/>
          <stop offset="1" stop-color="var(--label-cream)"/>
        </linearGradient>
        <path id="nameArc" d="M 35 250 Q 220 70 405 250"/>
      </defs>
      <path d="M0 70 C0 36 22 28 52 24 Q220 0 388 24 C418 28 440 36 440 70 V860 H0 Z" fill="url(#labelFill)"/>
      <text class="estate-name" text-anchor="middle">
        <textPath href="#nameArc" startOffset="50%">THORNFIELD</textPath>
      </text>
    </svg>
    <span class="estate-dot"></span>
    <div class="vineyard-vignette" role="img" aria-label="Engraved sketch of a country villa overlooking rows of vines"></div>
    <h1 class="wine-type">VINEYARDS</h1>
    <span class="rule rule-upper"></span>
    <p class="tasting-note">Crafted in small batches for family and friends, aged slowly in oak and shared around the table with good company.</p>
    <span class="rule rule-lower"></span>
    <p class="volume">750ML</p>
  </section>
</main>
</body>
</html>
```